Corvane Holdings , new business card design

investment firm with corporate clients . need double sided business card , vertical and horizontal options ,logo must be clear. prefer pantone colors only and sharp design. website also www.corvane.ae

Khalid Bin Tarrafi
Managing Director
Tel. +971 4 387 2940
Mobile +971 50 518 2403
khalid@corvane.ae
Q-Span Plaza, officw 18-B07, Warqa Gardens, Dubai

Contact Information for Business Card

Khalid Bin Tarrafi
Managing Director

Font styles to use
Serif

Colors

Designer to choose colors to be used in the design.

```html
<!DOCTYPE html>
<html lang="en">
<head>
<meta charset="utf-8">
<title>Corvane Holdings – Business Card</title>
<link href="https://fonts.googleapis.com/css2?family=Lato:wght@300;400;700&display=swap" rel="stylesheet">
<style>
  :root {
    --backdrop: #e6e3df;
    --card: #ffffff;
    --navy: #0f2d6b;
    --steel: #4a6f99;
    --ink: #2b2b2b;
    --muted: #5a5a5a;
    --rule: #b9b9b9;
    --swoosh-grey: #9a9a9a;
  }
  * { box-sizing: border-box; margin: 0; padding: 0; }
  html, body {
    width: 1200px; height: 997px; overflow: hidden;
    background: var(--backdrop);
    font-family: "Lato", sans-serif;
  }
  .sheet {
    position: relative; width: 1200px; height: 997px;
    display: flex; align-items: center; justify-content: center; gap: 60px;
  }
  .card {
    position: relative; width: 520px; height: 297px;
    background: var(--card);
    box-shadow: 0 2px 10px rgba(0,0,0,0.12);
    overflow: hidden;
  }
  .card__art { position: absolute; inset: 0; width: 100%; height: 100%; }
  .wordmark {
    display: flex; align-items: center; gap: 8px;
    font-weight: 300; color: var(--steel);
    letter-spacing: 0.22em; text-transform: uppercase;
  }
  .wordmark__square { width: 10px; height: 10px; background: var(--steel); }
  .card--front .wordmark { position: absolute; left: 30px; top: 42px; font-size: 17px; }
  .holder { position: absolute; right: 30px; top: 38px; text-align: right; }
  .holder__name { font-weight: 700; color: var(--navy); font-size: 16px; }
  .holder__title {
    font-size: 12px; color: var(--muted); margin-top: 2px;
    padding-bottom: 5px; border-bottom: 1px solid var(--rule); padding-left: 60px;
  }
  .holder__address { font-size: 11.5px; color: var(--muted); margin-top: 16px; line-height: 1.45; }
  .divider { position: absolute; left: 30px; top: 82px; width: 200px; height: 1px; background: var(--rule); }
  .website {
    position: absolute; right: 20px; top: 150px;
    font-size: 11px; color: #fff; letter-spacing: 0.2em;
  }
  .contacts { position: absolute; left: 30px; top: 196px; list-style: none; }
  .contacts__item {
    display: flex; align-items: center; gap: 7px;
    font-size: 13px; color: var(--muted); line-height: 20px;
  }
  .contacts__icon { width: 12px; height: 12px; flex: none; }
  .card--back { display: flex; align-items: center; justify-content: center; }
  .card--back .wordmark { font-size: 24px; }
  .card--back .wordmark__square { width: 13px; height: 13px; }
</style>
</head>
<body>
<main class="sheet">

  <section class="card card--front" aria-label="Card front">
    <svg class="card__art" viewBox="0 0 520 297" aria-hidden="true">
      <path d="M108,297 C210,212 320,180 520,178 L520,186 C330,190 220,225 128,297 Z" fill="var(--swoosh-grey)"/>
      <path d="M120,297 C220,200 330,146 520,142 L520,174 C360,176 250,222 168,297 Z" fill="var(--navy)"/>
    </svg>

    <div class="wordmark"><span class="wordmark__square"></span>Corvane Holdings</div>
    <div class="divider"></div>

    <div class="holder">
      <p class="holder__name">Khalid Bin Tarrafi</p>
      <p class="holder__title">Managing Director</p>
      <p class="holder__address">Q-Span Plaza, officw 18-B07,<br>Warqa Gardens, Dubai</p>
    </div>

    <p class="website">www.corvane.ae</p>

    <ul class="contacts">
      <li class="contacts__item">
        <svg class="contacts__icon" viewBox="0 0 12 12"><rect width="12" height="12" fill="var(--navy)"/><path d="M3.5,2.5 L5,2.5 L5.6,4.4 L4.7,5 C5.2,6.1 5.9,6.8 7,7.3 L7.6,6.4 L9.5,7 L9.5,8.5 C6,8.7 3.3,6 3.5,2.5 Z" fill="#fff"/></svg>
        +971 4 387 2940
      </li>
      <li class="contacts__item">
        <svg class="contacts__icon" viewBox="0 0 12 12"><rect width="12" height="12" fill="var(--navy)"/><rect x="4" y="2" width="4" height="8" rx="0.8" fill="none" stroke="#fff" stroke-width="1"/></svg>
        +971 50 518 2403
      </li>
      <li class="contacts__item">
        <svg class="contacts__icon" viewBox="0 0 12 12"><rect width="12" height="12" fill="var(--navy)"/><rect x="2.5" y="3.5" width="7" height="5" fill="none" stroke="#fff" stroke-width="0.9"/><path d="M2.5,3.5 L6,6.3 L9.5,3.5" fill="none" stroke="#fff" stroke-width="0.9"/></svg>
        khalid@corvane.ae
      </li>
    </ul>
  </section>

  <section class="card card--back" aria-label="Card back">
    <div class="wordmark"><span class="wordmark__square"></span>Corvane Holdings</div>
  </section>

</main>
</body>
</html>
```